Lakeshore Claim Partners Business card

We need to get business card Design for our Company we are Public Adjusters in Chicago Illinois - i like to see good combination and elements from my Company Logo. as well To be an two side design
Updates

Target Market(s)

Home /Business owner Property Managers

Industry/Entity Type

Business

Contact Information for Business Card

to show the Element of our logo i will Like 3D

Font styles to use
Sans Serif

Requirements
Must have
• Logo and Element of the Logo in 3D
Nice to have
• Logo That we Provide 3D Same Colors or open for suggestions
Should not have
• unleare view -

```html
<!DOCTYPE html>
<html lang="en">
<head>
<meta charset="utf-8">
<title>Lakeshore Claim Partners – Business Card</title>
<link rel="stylesheet" href="https://fonts.googleapis.com/css2?family=Montserrat:wght@400;500;700;800&display=swap">
<style>
  :root {
    --stage: #2b2b2d;
    --card-white: #ffffff;
    --navy: #0d2a7a;
    --navy-deep: #0a1f5e;
    --blue-light: #4a7fc4;
    --blue-mid: #1d47a6;
    --red: #e8242c;
    --text-blue: #1d3f9e;
  }
  * { box-sizing: border-box; margin: 0; padding: 0; }
  html, body {
    width: 1200px; height: 900px; overflow: hidden;
    background: var(--stage);
    font-family: "Montserrat", sans-serif;
  }
  .canvas { position: relative; width: 1200px; height: 900px; }
  .card {
    position: absolute; left: 250px; width: 700px; height: 400px;
    background: var(--card-white); overflow: hidden;
    box-shadow: 0 14px 30px rgba(0,0,0,.5);
  }
  .card--front { top: 40px; }
  .card--back { top: 470px; }
  .card-art { position: absolute; inset: 0; width: 700px; height: 400px; }

  /* front */
  .front-brand {
    position: absolute; left: 0; right: 0; top: 0; bottom: 40px;
    display: flex; align-items: center; justify-content: center;
  }
  .brand-name {
    font-weight: 800; font-size: 34px; color: var(--navy);
    letter-spacing: .2px; white-space: nowrap;
  }

  /* back */
  .back-brand {
    position: absolute; left: 40px; top: 62px;
  }
  .back-brand .brand-name { font-size: 26px; color: var(--card-white); }

  .holder { position: absolute; left: 40px; bottom: 34px; color: var(--text-blue); }
  .holder-name { font-weight: 700; font-size: 24px; letter-spacing: 1px; }
  .holder-role { color: var(--red); font-size: 15px; font-weight: 500; margin: 2px 0 6px; }
  .holder-address { font-size: 15px; line-height: 1.35; }

  .contact-list {
    position: absolute; right: 36px; top: 210px; list-style: none;
    color: var(--text-blue); font-size: 15px; line-height: 1.6; text-align: right;
  }
  .contact-list li { display: flex; justify-content: flex-end; align-items: center; gap: 8px; }
  .contact-icon { width: 12px; height: 12px; flex: none; }
</style>
</head>
<body>
<div class="canvas">

  <!-- Front side -->
  <section class="card card--front" aria-label="Card front">
    <svg class="card-art" viewBox="0 0 700 400" aria-hidden="true">
      <rect x="0" y="392" width="700" height="8" fill="var(--blue-mid)"/>
      <path d="M250 400 L272 374 H448 L470 400 Z" fill="var(--navy)"/>
    </svg>
    <div class="front-brand">
      <span class="brand-name">Lakeshore Claim Partners</span>
    </div>
  </section>

  <!-- Back side -->
  <section class="card card--back" aria-label="Card back">
    <svg class="card-art" viewBox="0 0 700 400" aria-hidden="true">
      <defs>
        <linearGradient id="bandFade" x1="0" y1="0" x2="0" y2="1">
          <stop offset="0" stop-color="var(--blue-light)"/>
          <stop offset="1" stop-color="var(--navy-deep)"/>
        </linearGradient>
      </defs>
      <path d="M0 0 H700 V160 H430 L400 195 H0 Z" fill="url(#bandFade)"/>
      <path d="M0 195 H400 L430 160 H700 V174 H436 L406 209 H0 Z" fill="var(--red)"/>
    </svg>

    <div class="back-brand">
      <span class="brand-name">Lakeshore Claim Partners</span>
    </div>

    <ul class="contact-list">
      <li>+00 7315 820 644
        <svg class="contact-icon" viewBox="0 0 12 12"><rect x="3" y="0.5" width="6" height="11" rx="1.2" fill="none" stroke="var(--red)" stroke-width="1.4"/></svg></li>
      <li>+00 2046 917 158
        <svg class="contact-icon" viewBox="0 0 12 12"><path d="M2 1 L4.5 1 L5.5 4 L4 5 C5 7 6 8 7.5 8.5 L8.5 7 L11 8 V10.5 C6 11 1 6 2 1 Z" fill="var(--red)"/></svg></li>
      <li>info@lakeshoreclaims.co.uk
        <svg class="contact-icon" viewBox="0 0 12 12"><rect x="0.7" y="2.2" width="10.6" height="7.6" rx="1" fill="none" stroke="var(--red)" stroke-width="1.3"/><path d="M1 3 L6 7 L11 3" fill="none" stroke="var(--red)" stroke-width="1.3"/></svg></li>
      <li>www.lakeshoreclaims.com
        <svg class="contact-icon" viewBox="0 0 12 12"><circle cx="6" cy="6" r="5" fill="none" stroke="var(--red)" stroke-width="1.3"/><path d="M1 6 H11 M6 1 C3.5 4 3.5 8 6 11 M6 1 C8.5 4 8.5 8 6 11" fill="none" stroke="var(--red)" stroke-width="1"/></svg></li>
    </ul>

    <div class="holder">
      <p class="holder-name">OWEN HARLOW</p>
      <p class="holder-role">Managing Director</p>
      <p class="holder-address">1450 Lakeview Park Rd<br>Ste 210, Evanston, IL 60201</p>
    </div>
  </section>

</div>
</body>
</html>
```